Full 10+ Page Online Learning eBook Design - NOT just the cover :)

We currently have an eBook within the online learning space which is geared towards a consumer audience (hobbyists, interests), but we have a new 2.0 version which is geared towards professionals (certifications, training, continuing ed, career-oriented). We need a new design and need the words/copy put into the eBook, but want to keep the look and feel of the original (open to variations in design). File is attached, along with various logo options.

Target Market(s)

Professionals

Industry/Entity Type

Learning

Font styles to use
Sans Serif

Colors
33a6d7
acd036
919191

Requirements
Must have
• Must follow a very similar look a feel of the original file. We use a lot of fonts like Raleway, Gotham, Helvetica Neue, Gil Sans, DIN - anything modern looking. We also use a lot of grayish hexagons in our corporate design. Feel free to check out brightlanternhub.example to get a better sense.
Nice to have
• Include some professionally oriented icons / photos
Should not have
• No cartoonish graphics or imagery

```html
<!DOCTYPE html>
<html lang="en">
<head>
<meta charset="utf-8">
<title>Packaging Options</title>
<link rel="stylesheet" href="https://fonts.googleapis.com/css2?family=Lato:wght@400;700&display=swap">
<style>
  :root {
    --brand-blue: #33a6d7;
    --brand-green: #acd036;
    --brand-grey: #919191;
    --ink: #1e1e1e;
    --paper: #ffffff;
    --night-deep: #07090d;
    --night-mid: #18242a;
    --night-teal: #3d6e74;
    --lamp-amber: #a87a3a;
  }
  * { box-sizing: border-box; margin: 0; padding: 0; }
  html, body { width: 852px; height: 1200px; overflow: hidden; background: var(--paper); }
  .page {
    position: relative;
    width: 852px;
    height: 1200px;
    overflow: hidden;
    background: var(--paper);
    font-family: "Lato", "Gill Sans", sans-serif;
    color: var(--ink);
  }
  .top-band {
    position: absolute; left: 0; top: 0;
    width: 852px; height: 16px;
    background: var(--brand-blue);
  }
  .section-title {
    position: absolute; left: 7px; top: 44px;
    font-size: 21px; font-weight: 400;
    letter-spacing: 0.6px;
    color: var(--ink);
  }
  .title-rule {
    position: absolute; left: 7px; top: 75px;
    width: 840px; height: 3px;
    background: var(--brand-blue);
  }
  .body-copy {
    position: absolute; left: 7px; top: 90px;
    width: 836px;
    font-size: 15.4px;
    line-height: 21.6px;
    color: var(--ink);
  }
  .body-copy p, .body-copy ul { margin-bottom: 21.6px; }
  .body-copy ul { list-style: none; }
  .body-copy li::before { content: "\2022\00a0"; }
  .hex-accent {
    position: absolute; right: 0; top: 540px;
    width: 420px; height: 226px;
    background: radial-gradient(ellipse at 75% 70%, rgba(145,145,145,0.16), rgba(51,166,215,0.06) 45%, rgba(255,255,255,0) 75%);
  }
  .night-photo {
    position: absolute; left: 0; top: 766px;
    width: 852px; height: 434px;
    background:
      radial-gradient(ellipse at 20% 30%, rgba(168,122,58,0.55), rgba(168,122,58,0) 30%),
      radial-gradient(ellipse at 50% 85%, rgba(61,110,116,0.65), rgba(61,110,116,0) 55%),
      linear-gradient(180deg, var(--night-deep) 0%, var(--night-mid) 55%, var(--night-teal) 100%);
  }
</style>
</head>
<body>
<div class="page">
  <div class="top-band"></div>
  <h1 class="section-title">PACKAGING OPTIONS</h1>
  <div class="title-rule"></div>

  <div class="body-copy">
    <p>We've seen a high correlation between learning and buying. When somebody wants to polish skills, reach new levels of professional advancement or complete a new credential, he or she also is more inclined to attain the materials required to achieve that goal. That tendency makes for excellent opportunities to upsell and cross-sell. That's where packaging comes in -- the ability to:</p>
    <ul>
      <li>Combine courses into bundles;</li>
      <li>Create and promote discount and trial coupons;</li>
      <li>Manage affiliate selling;</li>
      <li>Suggest related content for cross-selling;</li>
      <li>Enable users to build their own packages of content; and</li>
      <li>Continue promoting and selling to the same buyers to help them build on their successes.</li>
    </ul>
    <p>You're probably familiar with the concept of the customer lifetime value (CLV), which attempts to describe the entire lifecycle of your customer acquisition and retention. Maintaining an eye on CLV helps you to determine the appropriate investment for acquiring a new customer and improves your ability to monitor how well your relationship-building efforts are going.</p>
    <p>In the business of online learning, however, we prefer to use the model of "Learner Lifetime Value" or LLV. This metric takes all the same inputs as CLV with one key difference: It incorporates both the individual learner sales and the recurring corporate subscription revenues in order to measure the overall success of your online learning operation. (You can read about the four levers that play an important role in that metric in this article.)</p>
    <p>The point is this: In order to maximize LLV, your learning platform needs to provide you with agility and flexibility and the same kind of functionality customers expect in their other kinds of e-commerce transactions. If it takes you a month programmatically to create a holiday bundle, for instance, you may find that your most creative ideas for extending LLV never get off the ground. You need the tools at hand to allow you to quickly bundle, print, package, model, upsell and cross-sell your online courses.</p>
  </div>

  <div class="hex-accent" role="img" aria-label="Faint grey and blue hexagon pattern decoration"></div>

  <div class="night-photo" role="img" aria-label="Photograph of a wet city street at night with tram tracks, a lit advertising column and a church in the distance"></div>
</div>
</body>
</html>
```